National Water and Fire Restoration, Multi Surface Cleaning, Carpet Cleaning Business Needs a Websi

We need a new fresh website for our business. There are multiple services we offer and we need a fresh corporate website that represents us better. We start from cleaning carpet and tiles, to upholstery and curtains, to completely clean all contents and building materials after a fire, or completely dry out a home or business after a major or minor flood event. We are open to all concepts as we want to create a new look, maybe even logo, signage, vehicle signage, uniforms.
We are open to new colours etc.

Go to www.brightvaleclean.com.au for current logo and all other past ideas

Reason: I need to see more quality designs to sink my teeth into

Target Market(s)

The target market is everyone of all walks of life

Industry/Entity Type

Business

Number of Pages Required

3 page

Font styles to use
Sans Serif

Requirements
Must have
• Home page
• Services page
• Contact us page
• The rest is up to your imagination
• ***This is design only - NO CODING REQUIRED***
Nice to have
• Pictures

```html
<!DOCTYPE html>
<html lang="en">
<head>
<meta charset="utf-8">
<title>Brightvale Clean — Home</title>
<link rel="stylesheet" href="https://fonts.googleapis.com/css2?family=Oxygen:wght@400;700&family=Roboto:wght@400;500&display=swap">
<style>
:root{
  --blue:#0d4f9c;
  --blue-dark:#0a3f7e;
  --pink:#e0197d;
  --ink:#222;
  --grey:#eeeeee;
  --grey-line:#d4d4d4;
  --charcoal:#333;
  --white:#fff;
}
*{box-sizing:border-box;margin:0;padding:0}
html,body{width:881px;height:1200px;overflow:hidden;background:var(--white)}
body{position:relative;font-family:"Oxygen",sans-serif;color:var(--ink)}
.abs{position:absolute}

/* header */
.brand{left:105px;top:12px;display:flex;align-items:center;gap:8px}
.brand-mark{width:40px;height:40px;border-radius:50%;background:var(--blue)}
.brand-name{font-size:22px;font-weight:700;color:var(--blue)}
.tagline{left:106px;top:66px;font-size:9px;color:var(--pink);font-style:italic}
.social-btn{left:660px;top:9px;width:110px;height:25px;background:var(--blue);color:var(--white);font-size:11px;display:flex;align-items:center;justify-content:center;border-radius:2px}
.phone{right:147px;top:41px;text-align:right;font-size:12.5px;line-height:15.5px}
.phone-icon{left:744px;top:42px}

/* nav — sits above the hero frame */
.nav{left:102px;top:80px;width:677px;height:28px;background:#f4f4f4;border:1px solid var(--grey-line);display:flex;font-size:11.5px;color:var(--blue);z-index:5;box-shadow:0 2px 3px rgba(0,0,0,.18)}
.nav a{display:flex;align-items:center;justify-content:center;border-right:1px solid var(--grey-line);text-decoration:none;color:inherit;white-space:nowrap}
.nav a:last-child{border-right:0}
.nav .active{background:var(--pink);color:var(--white);margin:2px 0 2px 2px}

/* hero */
.hero-frame{left:60px;top:93px;width:762px;height:301px;border:1px solid var(--grey-line);z-index:1}
.hero-photo{left:63px;top:97px;width:755px;height:293px;background:linear-gradient(180deg,#6b6d6a 0%,#3f4a4f 45%,#6a5550 75%,#8a6a66 100%);z-index:1}
.hero-caption{left:63px;top:350px;width:755px;height:40px;background:rgba(20,20,20,.6);color:var(--white);font-family:"Roboto",sans-serif;font-size:18px;padding:10px 0 0 42px;z-index:2}
.hero-arrow{top:361px;width:22px;height:22px;background:var(--blue);z-index:3}

/* services */
.section-title{left:0;width:881px;top:418px;text-align:center;font-size:25px;font-weight:700;color:var(--blue)}
.section-intro{left:110px;width:661px;top:448px;text-align:center;font-size:10.5px;line-height:16px}
.service{top:515px;width:150px;height:134px;border:1px solid var(--grey-line)}
.service-inner{position:absolute;left:4px;top:4px;right:4px;bottom:4px;background:var(--grey)}
.service-photo{position:absolute;left:13px;top:-17px;width:122px;height:105px;background:var(--white);border:1px solid var(--grey-line);padding:3px}
.service-photo div{width:100%;height:100%}
.service-name{position:absolute;left:0;width:100%;top:92px;text-align:center;font-size:9.5px;line-height:11px;text-transform:uppercase;color:#333}
.read-btn{position:absolute;left:45px;top:123px;width:58px;height:18px;background:var(--pink);color:var(--white);font-size:8.5px;display:flex;align-items:center;justify-content:center;outline:2px solid var(--white)}
.carousel-arrow{top:567px}

/* tabs */
.tabs{left:102px;top:692px;width:432px;height:162px;border:1px solid var(--grey-line)}
.tab-row{display:flex;height:28px;font-size:10.5px}
.tab-row span{display:flex;align-items:center;padding:0 10px;border-right:1px solid var(--grey-line);border-bottom:1px solid var(--grey-line)}
.tab-row .current{color:var(--blue);border-bottom:0;background:var(--grey);margin:2px 0 0 3px;padding:0 12px}
.tab-panel{position:absolute;left:3px;top:28px;width:424px;height:128px;background:var(--grey);padding:8px 10px;font-size:9.8px;line-height:12.9px;text-align:justify}
.tab-more{position:absolute;right:12px;bottom:8px;font-size:9.5px;color:var(--pink)}
.promo{left:546px;top:694px;width:233px;height:160px;border:1px solid var(--grey-line);padding:3px}
.promo div{width:100%;height:100%;background:linear-gradient(135deg,#5a6a3a,#3b4a2c 60%,#8a7a5a)}

/* enquiry */
.enquiry{left:101px;top:867px;width:678px;height:122px;background:var(--grey);border:1px solid var(--grey-line)}
.enquiry-head{left:101px;top:867px}
.enquiry-title{left:110px;top:896px;color:var(--white);font-family:"Roboto",sans-serif;font-size:21px}
.enquiry-sub{left:110px;top:925px;color:var(--white);font-family:"Roboto",sans-serif;font-size:12.5px;line-height:16px}
.field{background:var(--white);border:1px solid #ddd;font-size:8.5px;color:#888;padding:5px 5px}
.send{background:var(--pink);color:var(--white);font-size:10px;display:flex;align-items:center;justify-content:center}

/* footer */
.footer{left:0;top:1013px;width:881px;height:147px;background:var(--blue)}
.f-title{color:var(--white);font-family:"Roboto",sans-serif;font-size:12px;font-weight:500}
.f-links{color:var(--white);font-size:8.5px;line-height:15.7px;list-style:none}
.f-links li::before{content:"• ";color:#8fb4e6}
.f-divider{width:1px;background:#2f6ab3;top:1035px;height:104px}
.badge{background:#c9d7ea}
.bottom{left:0;top:1160px;width:881px;height:40px;background:#ececec}
.copy{left:101px;top:1181px;font-size:9px}
.deal{left:340px;top:1170px;font-size:8.5px;text-align:right;line-height:11px;color:#444}
.deal b{color:var(--blue)}
.hint{left:486px;top:1179px;font-size:8.5px;color:#444;display:flex;align-items:center;gap:4px}
.like{border:1px solid #bbb;background:var(--white);padding:1px 4px;font-size:8px}
</style>
</head>
<body>

<header>
  <div class="abs brand"><span class="brand-mark"></span><span class="brand-name">Brightvale Clean</span></div>
  <div class="abs tagline">we don't cut corners - we clean them.</div>
  <div class="abs social-btn">Find us on Social</div>
  <div class="abs phone">Phone : 4055 0198<br>0400 555 217</div>
  <svg class="abs phone-icon" width="26" height="26" viewBox="0 0 26 26" aria-hidden="true">
    <rect x="2" y="1" width="15" height="22" rx="2" fill="var(--pink)"/>
    <rect x="5" y="4" width="9" height="13" fill="#fff"/>
    <path d="M15 10h6l-3-3M21 10l-3 3" stroke="var(--pink)" stroke-width="2.5" fill="none"/>
  </svg>
  <nav class="abs nav">
    <a class="active" style="width:53px">Home</a>
    <a style="width:76px">About Us</a>
    <a style="width:70px">Services</a>
    <a style="width:94px">Commercial</a>
    <a style="width:108px">Schedule a Job</a>
    <a style="width:114px">Referral Program</a>
    <a style="width:58px">Links</a>
    <a style="width:102px">Contact Us</a>
  </nav>
</header>

<section>
  <div class="abs hero-frame"></div>
  <div class="abs hero-photo" role="img" aria-label="Office lounge with blue armchairs on striped carpet"></div>
  <div class="abs hero-caption">We provide you with the most outstanding service experience EVER!</div>
  <svg class="abs hero-arrow" style="left:729px" viewBox="0 0 22 22" aria-hidden="true"><path d="M13 6l-5 5 5 5" stroke="#fff" stroke-width="1.6" fill="none"/></svg>
  <svg class="abs hero-arrow" style="left:754px" viewBox="0 0 22 22" aria-hidden="true"><path d="M9 6l5 5-5 5" stroke="#fff" stroke-width="1.6" fill="none"/></svg>
</section>

<section>
  <h2 class="abs section-title">Our Services</h2>
  <p class="abs section-intro">Sablage de plancher artisanal ou teinture, notre expertise et notre professionnalisme sont reconnus aupres de notre clientele. L'equipement ultramoderne que nous utilisons et que nous avons nous-memes perfectionne temoigne de notre souci d'innover.</p>

  <svg class="abs carousel-arrow" style="left:64px" width="33" height="33" viewBox="0 0 33 33" aria-hidden="true"><circle cx="16.5" cy="16.5" r="14.5" fill="#fff" stroke="#5b86bf" stroke-width="2.5"/><path d="M19 9l-7 7.5 7 7.5" stroke="#5b86bf" stroke-width="2.5" fill="none"/></svg>
  <svg class="abs carousel-arrow" style="left:784px" width="33" height="33" viewBox="0 0 33 33" aria-hidden="true"><circle cx="16.5" cy="16.5" r="14.5" fill="#fff" stroke="#5b86bf" stroke-width="2.5"/><path d="M14 9l7 7.5-7 7.5" stroke="#5b86bf" stroke-width="2.5" fill="none"/></svg>

  <div class="abs service" style="left:102px"><div class="service-inner"></div>
    <div class="service-photo"><div role="img" aria-label="Carpet cleaning wand on beige carpet" style="background:linear-gradient(135deg,#cfc8bb,#a39c90)"></div></div>
    <div class="service-name">Carpet<br>Cleaning</div><div class="read-btn">READ MORE</div></div>
  <div class="abs service" style="left:278px"><div class="service-inner"></div>
    <div class="service-photo"><div role="img" aria-label="Upholstery being steam cleaned" style="background:linear-gradient(135deg,#d9d4bf,#b8ae8e)"></div></div>
    <div class="service-name">Upholstery<br>Cleaning</div><div class="read-btn">READ MORE</div></div>
  <div class="abs service" style="left:454px"><div class="service-inner"></div>
    <div class="service-photo"><div role="img" aria-label="Technician drying a water damaged carpet" style="background:linear-gradient(135deg,#7a6a52,#3f6a6a)"></div></div>
    <div class="service-name">Water Damage<br>Specialist</div><div class="read-btn">READ MORE</div></div>
  <div class="abs service" style="left:630px"><div class="service-inner"></div>
    <div class="service-photo"><div role="img" aria-label="Before and after view of cleaned brick paving" style="background:linear-gradient(135deg,#8a5a3a,#b5713f)"></div></div>
    <div class="service-name">Natural Stone<br>Cleaning</div><div class="read-btn">READ MORE</div></div>
</section>

<section>
  <div class="abs tabs">
    <div class="tab-row"><span class="current">ABOUT US</span><span>6 REASONS TO CHOOSE US</span><span>TESTIMONIALS</span></div>
    <div class="tab-panel">Brightvale Clean is a professional, full-service carpet, floor, fabric care company serving the North Queensland areas including Cairns, Tablelands, Port Douglas and Mission Beach. Brightvale Carpet Cleaning has been in business since 1996. At Brightvale Clean, we take pride in our reputation, experience, education, systems, and guarantee. Brightvale Clean is an NCRB certified firm, the world's most recognized body of certification for carpet and upholstery cleaners. You can depend on us at Brightvale Carpet Cleaning Services for carpet cleaning, upholstery cleaning, oriental and area rug cleaning, fiber and fabric protection, tile and grout cleaning and sealing, natural stone.
      <span class="tab-more">READ MORE</span></div>
  </div>
  <div class="abs promo"><div role="img" aria-label="Introductory offer banner with a child outdoors, inviting visitors to learn about the introductory offer"></div></div>
</section>

<section>
  <div class="abs enquiry"></div>
  <svg class="abs enquiry-head" width="207" height="122" viewBox="0 0 207 122" aria-hidden="true"><path d="M0 0H160L207 61L160 122H0Z" fill="var(--charcoal)"/></svg>
  <div class="abs enquiry-title">QUICK ENQUIRY</div>
  <div class="abs enquiry-sub">Fill out the form below and we<br>will contac you within 24hrs.</div>
  <div class="abs field" style="left:326px;top:878px;width:209px;height:20px">Name</div>
  <div class="abs field" style="left:326px;top:905px;width:209px;height:20px">Email</div>
  <div class="abs field" style="left:326px;top:933px;width:209px;height:20px">Phone</div>
  <div class="abs field" style="left:545px;top:877px;width:215px;height:77px">Message</div>
  <div class="abs send" style="left:698px;top:961px;width:64px;height:20px">SEND</div>
</section>

<footer>
  <div class="abs footer"></div>
  <div class="abs f-title" style="left:103px;top:1034px">QUICK LINKS</div>
  <ul class="abs f-links" style="left:103px;top:1055px"><li>Home</li><li>About Us</li><li>Services</li><li>Commercial</li><li>Links</li></ul>
  <ul class="abs f-links" style="left:183px;top:1055px"><li>Schedule a Job</li><li>Referral Program</li><li>Contact Us</li></ul>
  <div class="abs f-divider" style="left:272px"></div>
  <div class="abs f-title" style="left:290px;top:1034px">NEWSLETTER UPDATES</div>
  <div class="abs" style="left:290px;top:1053px;width:190px;font-size:8.5px;line-height:11.5px;color:#fff">Lorem ipsum dolor sit amet, consectetur adip iscing elit, sed do eiusmod tempor incididunt</div>
  <div class="abs field" style="left:290px;top:1081px;width:184px;height:21px">@ &nbsp;| Your E-mail</div>
  <div class="abs send" style="left:290px;top:1108px;width:46px;height:22px">SEND</div>
  <div class="abs f-divider" style="left:490px"></div>
  <div class="abs badge" style="left:509px;top:1038px;width:66px;height:34px;border-radius:4px"></div>
  <div class="abs badge" style="left:590px;top:1033px;width:34px;height:38px;border-radius:50%"></div>
  <div class="abs badge" style="left:512px;top:1083px;width:46px;height:38px"></div>
  <div class="abs badge" style="left:585px;top:1080px;width:42px;height:42px;border-radius:50%"></div>
  <div class="abs" style="left:500px;top:1130px;font-size:8px;color:#fff">We don't cut corners. We clean them.</div>
  <div class="abs f-divider" style="left:653px"></div>
  <div class="abs badge" style="left:674px;top:1037px;width:87px;height:85px;border-radius:3px"></div>
  <div class="abs" style="left:675px;top:1126px;font-size:12px;color:#dbe6f5">Certified Firm</div>

  <div class="abs bottom"></div>
  <div class="abs copy">© 2014 <b>BrightvaleClean.</b> All Rights Reserved.</div>
  <div class="abs deal"><b>10%</b> Discount on all services<br>on top of any other offer</div>
  <div class="abs" style="left:476px;top:1170px;width:1px;height:22px;background:#ccc"></div>
  <div class="abs hint">Hint: Only If You <span class="like">Like</span> Us</div>
  <div class="abs social-btn" style="top:1166px;left:667px">Find us on Social</div>
</footer>

</body>
</html>
```